Supplement Brand Product Labels

Product Label for Supplement Brand

Protein Powder Label (2 x different flavours)

Neon Colours / Skull / Spooky
Refer to pictures below, they are the look we are wanting to go with but put our touch to it aswell.

Target Market(s)

Fitness

Industry/Entity Type

Supplement Brand

Colors
0054AA
0677BA
7BADD7
CADEEF
E8F1F8
0094D4
00A9DD
6FCCEA
C7EBF8
E9F6FB
00AB8E
00BBA5
67D7C9
C6EFE9
E9F9F6
59FF00
82FF00
B8FF75
E3FFCB
F4FFEA
FFF300
FFF600
FEFA6F
FFFEC7
FFFEE8
FFC000
F8CF3A
FAE287
FDF2CF
FEFAEE
F0912C
F2A743
F7CA91
FBE8D2
FDF5EE
EE7325
F08F49
F5BC92
FAE3D3
FDF4ED
EB3D1F
EC4F4E
F09395
F8D3D4
FCEDEE
E54698
E96AAD
F1A4CE
F9D9EA
FCEFF6
A7469A
B969AE
D3A5CF
EDDBEB
F8F0F9
6B429C
8869AF
B7A5CE
E3DAEB
F3F0F8

Requirements
Nice to have
• Skull, Neon Colours, Abstract, Barbell, Lighting Bolt, Flames, Spooky

```html
<!DOCTYPE html>
<html lang="en">
<head>
<meta charset="utf-8">
<title>Voltra Supps – Product Labels</title>
<link rel="stylesheet" href="https://fonts.googleapis.com/css2?family=Permanent+Marker&family=Roboto+Condensed:wght@400;700&display=swap">
<style>
  :root{
    --page:#e9e9e9;
    --label-bg:#050605;
    --panel:#0b0d0b;
    --neon:#59ff00;
    --neon-soft:#82ff00;
    --neon-pale:#b8ff75;
    --white:#ffffff;
    --grey:#b9b9b9;
    --rule:#3a3a3a;
  }
  *{box-sizing:border-box;margin:0;padding:0}
  html,body{width:800px;height:1200px;overflow:hidden}
  body{background:var(--page);font-family:"Roboto Condensed",Arial,sans-serif;color:var(--white);
    display:flex;flex-direction:column;justify-content:center;align-items:center;gap:48px}
  .label{position:relative;width:760px;height:272px;background:var(--label-bg);overflow:hidden;
    display:grid;grid-template-columns:210px 1fr 210px}
  .label-art{position:absolute;left:150px;top:0;width:460px;height:272px;
    background:radial-gradient(ellipse 50% 62% at 50% 55%, #3fbf14 0%, #1c6a0a 32%, #0a2a05 60%, rgba(5,6,5,0) 100%)}
  .panel{position:relative;z-index:1;padding:16px 16px 12px;font-size:7.5px;line-height:1.45;color:var(--grey)}
  .panel-left{display:flex;flex-direction:column}
  .panel-title{font-weight:700;font-size:10px;color:var(--neon);margin-bottom:6px}
  .panel p{margin-bottom:6px}
  .brand-small{margin-top:auto;font-family:"Permanent Marker",cursive;font-size:20px;line-height:1;color:var(--white)}
  .website{margin-top:4px;font-size:7px;color:var(--grey)}
  .front{position:relative;z-index:1;display:flex;flex-direction:column;align-items:center;padding-top:22px;text-align:center}
  .brand-logo{font-family:"Permanent Marker",cursive;color:var(--white);font-size:54px;line-height:0.9;letter-spacing:1px}
  .brand-logo span{display:block;font-size:22px;letter-spacing:4px;margin-top:2px}
  .product-name{margin-top:auto;font-family:"Permanent Marker",cursive;line-height:0.95}
  .product-name .line-a{display:block;font-size:40px;color:var(--white)}
  .product-name .line-b{display:block;font-size:34px;color:var(--neon)}
  .product-name.long .line-a{font-size:38px;color:var(--neon)}
  .product-name.long .line-b{font-size:22px;color:var(--white);letter-spacing:1px}
  .net-weight{font-weight:700;font-size:13px;letter-spacing:1px;margin:8px 0 14px}
  .panel-right{display:flex;flex-direction:column}
  .nutrition{width:100%;border-collapse:collapse;font-size:7px;color:var(--grey)}
  .nutrition caption{text-align:left;font-weight:700;font-size:9px;color:var(--white);margin-bottom:3px}
  .nutrition th,.nutrition td{border-bottom:1px solid var(--rule);padding:2.5px 2px;text-align:right;font-weight:400}
  .nutrition th:first-child,.nutrition td:first-child{text-align:left}
  .nutrition thead th{color:var(--white);font-weight:700}
  .ingredients-title{margin-top:10px;font-weight:700;font-size:9px;color:var(--neon)}
  .ingredients{font-size:7.5px;color:var(--grey)}
  .origin{margin-top:auto;display:flex;align-items:center;gap:6px;justify-content:flex-end;
    font-weight:700;font-size:9px;color:var(--white);letter-spacing:0.5px}
  .origin-badge{width:18px;height:18px;background:var(--neon)}
</style>
</head>
<body>

<section class="label">
  <div class="label-art" role="img" aria-label="Glowing green skull wrapped in neon smoke"></div>
  <div class="panel panel-left">
    <h3 class="panel-title">Directions Of Use</h3>
    <p>Mix 1 scoop (5g) with 300ml of water. Consume before, during or after training. Take up to twice daily.</p>
    <p>Formulated supplementary sports food. Not suitable for children under 15 or pregnant women. Should only be used under medical supervision.</p>
    <p>Store below 25°C in a cool, dry place.</p>
    <div class="brand-small">VOLTRA SUPPS</div>
    <div class="website">www.voltrasupps.com</div>
  </div>
  <div class="front">
    <div class="brand-logo">VOLTRA<span>SUPPS</span></div>
    <div class="product-name"><span class="line-a">BCAA</span><span class="line-b">2:1:1</span></div>
    <div class="net-weight">250G</div>
  </div>
  <div class="panel panel-right">
    <table class="nutrition">
      <caption>Nutrition Information</caption>
      <thead><tr><th>Servings per pack: 50<br>Serving size: 5g</th><th>Avg Qty Per Serving</th><th>Per 100g</th></tr></thead>
      <tbody>
        <tr><td>Energy</td><td>85kJ</td><td>1700kJ</td></tr>
        <tr><td>Protein</td><td>4.2g</td><td>84g</td></tr>
        <tr><td>Carbohydrate</td><td>0g</td><td>0g</td></tr>
        <tr><td>Sugars</td><td>0g</td><td>0g</td></tr>
        <tr><td>Fat</td><td>0g</td><td>0g</td></tr>
        <tr><td>Sodium</td><td>2mg</td><td>40mg</td></tr>
      </tbody>
    </table>
    <div class="ingredients-title">Ingredients</div>
    <div class="ingredients">Leucine, Isoleucine, Valine</div>
    <div class="origin"><span class="origin-badge"></span>MADE IN AUSTRALIA</div>
  </div>
</section>

<section class="label">
  <div class="label-art" role="img" aria-label="Glowing green skull wrapped in neon smoke"></div>
  <div class="panel panel-left">
    <h3 class="panel-title">Directions Of Use</h3>
    <p>Mix 1 scoop (3g) with 300ml of water. Consume before, during or after training. Take up to twice daily.</p>
    <p>Formulated supplementary sports food. Not suitable for children under 15 or pregnant women. Should only be used under medical supervision.</p>
    <p>Store below 25°C in a cool, dry place.</p>
    <div class="brand-small">VOLTRA SUPPS</div>
    <div class="website">www.voltrasupps.com</div>
  </div>
  <div class="front">
    <div class="brand-logo">VOLTRA<span>SUPPS</span></div>
    <div class="product-name long"><span class="line-a">CREATINE</span><span class="line-b">MONOHYDRATE</span></div>
    <div class="net-weight">250G</div>
  </div>
  <div class="panel panel-right">
    <table class="nutrition">
      <caption>Nutrition Information</caption>
      <thead><tr><th>Servings per pack: 83<br>Serving size: 3g</th><th>Avg Qty Per Serving</th><th>Per 100g</th></tr></thead>
      <tbody>
        <tr><td>Energy</td><td>0kJ</td><td>0kJ</td></tr>
        <tr><td>Protein</td><td>0g</td><td>0g</td></tr>
        <tr><td>Carbohydrate</td><td>0g</td><td>0g</td></tr>
        <tr><td>Sugars</td><td>0g</td><td>0g</td></tr>
        <tr><td>Fat</td><td>0g</td><td>0g</td></tr>
        <tr><td>Sodium</td><td>1mg</td><td>20mg</td></tr>
      </tbody>
    </table>
    <div class="ingredients-title">Ingredients</div>
    <div class="ingredients">Creatine Monohydrate</div>
    <div class="origin"><span class="origin-badge"></span>MADE IN AUSTRALIA</div>
  </div>
</section>

</body>
</html>
```